Unique Business Card Design

Unique Business Card design for our orthotic and prosthetic company. Our logo is on our website, color is light blue. Unique shape (artificial leg shaped, vertical, etc..) preferred. Logo, business name, individual name and basic demographics needed.

Industry/Entity Type

Business

Contact Information for Business Card

Logo, Industry, Phone # Logo, "Prosthetic & Orthotic Services" Place to add individual name and contact info

Colors
cee9f5

Requirements
Must have
• The icon must be there, placement of "Prosthetic & Orthotic Services" can be moved
Nice to have
• Like the mix of light blue, and a little darker blue. One design included the icons from my website which was a nice touch

```html
<!DOCTYPE html>
<html lang="en">
<head>
<meta charset="utf-8">
<title>Limbwell Inc. Business Card</title>
<link rel="stylesheet" href="https://fonts.googleapis.com/css2?family=Open+Sans:wght@400;600&family=Roboto:wght@400;500;700&family=Crimson+Text:ital@1&display=swap">
<style>
  :root {
    --stage: #e6e8ea;
    --card-dark: #2c2c2d;
    --card-light: #ffffff;
    --sky: #cee9f5;
    --brand-blue: #0b5aa8;
    --ink: #333538;
    --rule: #d8d8d8;
  }
  * { margin: 0; padding: 0; box-sizing: border-box; }
  html, body { width: 1200px; height: 1000px; overflow: hidden; }
  body { background: var(--stage); position: relative; font-family: "Roboto", sans-serif; }

  .card {
    position: absolute; left: 220px; width: 760px; height: 436px;
    border-radius: 30px; overflow: hidden;
  }
  .card--back { top: 50px; background: var(--card-dark); }
  .card--front { top: 524px; background: var(--card-light); }

  /* Back card */
  .back-brand { position: absolute; left: 122px; top: 128px; display: flex; align-items: center; }
  .back-brand__dot { width: 140px; height: 140px; border-radius: 50%; background: var(--sky); flex: none; }
  .back-brand__text { margin-left: 16px; }
  .back-brand__name {
    font-family: "Open Sans", sans-serif; font-weight: 400; font-size: 40px;
    color: var(--sky); line-height: 1; letter-spacing: 0.5px;
  }
  .back-brand__rule { height: 5px; background: var(--sky); margin: 10px 0 8px; width: 350px; }
  .back-brand__tagline {
    font-family: "Crimson Text", serif; font-style: italic; font-size: 23px;
    color: var(--sky); padding-left: 22px;
  }
  .back-url {
    position: absolute; left: 0; right: 0; top: 373px; text-align: center;
    font-family: "Roboto", sans-serif; font-size: 17px; color: #e4e4e4;
  }

  /* Front card */
  .front-shape { position: absolute; left: 0; top: 0; }
  .front-brand { position: absolute; left: 43px; top: 38px; display: flex; align-items: center; }
  .front-brand__dot { width: 88px; height: 88px; border-radius: 50%; background: var(--brand-blue); flex: none; }
  .front-brand__text { margin-left: 7px; }
  .front-brand__name {
    font-family: "Open Sans", sans-serif; font-weight: 400; font-size: 24px;
    color: var(--brand-blue); line-height: 1;
  }
  .front-brand__rule { height: 3px; background: var(--brand-blue); margin: 5px 0 4px; width: 214px; }
  .front-brand__tagline {
    font-family: "Crimson Text", serif; font-style: italic; font-size: 15px;
    color: var(--brand-blue); padding-left: 15px;
  }

  .person { position: absolute; left: 137px; top: 146px; }
  .person__name { font-weight: 700; font-size: 22px; color: var(--brand-blue); }
  .person__title { font-size: 16px; color: var(--ink); margin-top: 2px; }
  .person__rule { width: 190px; height: 1px; background: var(--rule); margin: 12px 0 14px; }
  .person__address { font-size: 17px; color: var(--ink); line-height: 22px; }

  .contact-list { list-style: none; margin-top: 14px; }
  .contact-list li {
    display: flex; align-items: center; font-size: 17px; color: var(--ink);
    height: 24.5px;
  }
  .contact-list svg { width: 13px; height: 13px; margin-right: 6px; fill: var(--brand-blue); flex: none; }
  .contact-list .accent { color: var(--brand-blue); }
</style>
</head>
<body>

<section class="card card--back">
  <div class="back-brand">
    <div class="back-brand__dot"></div>
    <div class="back-brand__text">
      <div class="back-brand__name">LIMBWELL INC.</div>
      <div class="back-brand__rule"></div>
      <div class="back-brand__tagline">Prosthetic &amp; Orthotic Services</div>
    </div>
  </div>
  <div class="back-url">www.limbwellinc.com</div>
</section>

<section class="card card--front">
  <svg class="front-shape" width="760" height="436" viewBox="0 0 760 436" aria-hidden="true">
    <circle cx="660" cy="221" r="245" fill="var(--brand-blue)"/>
  </svg>

  <div class="front-brand">
    <div class="front-brand__dot"></div>
    <div class="front-brand__text">
      <div class="front-brand__name">LIMBWELL INC.</div>
      <div class="front-brand__rule"></div>
      <div class="front-brand__tagline">Prosthetic &amp; Orthotic Services</div>
    </div>
  </div>

  <div class="person">
    <div class="person__name">Miriam Halden</div>
    <div class="person__title">CO LPO</div>
    <div class="person__rule"></div>
    <div class="person__address">2350 Harbor View Road<br>Riverton, NY 11590</div>
    <ul class="contact-list">
      <li><svg viewBox="0 0 16 16"><path d="M4 0h8a1 1 0 0 1 1 1v14a1 1 0 0 1-1 1H4a1 1 0 0 1-1-1V1a1 1 0 0 1 1-1zm1 2v10h6V2zm3 11a1 1 0 1 0 0 2 1 1 0 0 0 0-2z"/></svg>845-5550142</li>
      <li><svg viewBox="0 0 16 16"><path d="M3.5 0l3 3.5-2 2c1 2.2 2.8 4 5 5l2-2 3.5 3-2 3C6.5 14.5 1.5 9.5 1 2.5z"/></svg>(718) 555-0170</li>
      <li><svg viewBox="0 0 16 16"><path d="M4 0h8v4H4zM1 5h14v7h-3v4H4v-4H1zm4 5v4h6v-4z"/></svg>(718) 555-0139</li>
      <li><svg viewBox="0 0 16 16"><path d="M0 3h16v1.5L8 9 0 4.5zm0 3.2 8 4.5 8-4.5V13H0z"/></svg>mhalden@limbwellinc.com</li>
      <li><svg viewBox="0 0 16 16"><path d="M8 0a8 8 0 1 0 0 16A8 8 0 0 0 8 0zm0 1.5c.9 0 1.9 1.7 2.2 5.5H5.8C6.1 3.2 7.1 1.5 8 1.5zM1.6 7h2.7c.1-2 .4-3.6 1-4.7A6.5 6.5 0 0 0 1.6 7zm0 2a6.5 6.5 0 0 0 3.7 4.7c-.6-1.1-.9-2.7-1-4.7zm4.2 0c.3 3.8 1.3 5.5 2.2 5.5s1.9-1.7 2.2-5.5zm5.9 0c-.1 2-.4 3.6-1 4.7A6.5 6.5 0 0 0 14.4 9zm2.7-2a6.5 6.5 0 0 0-3.7-4.7c.6 1.1.9 2.7 1 4.7z"/></svg>www.<span class="accent">limbwellinc</span>.net</li>
    </ul>
  </div>
</section>

</body>
</html>
```